Kestrel Facilities Business Card Design

We would now like to design business cards with the new Kestrel Facilities logo

Target Market(s)

Professional

Industry/Entity Type

Professional services

Contact Information for Business Card

Employee name, title, phone number, email address, corporate office address and logo.

Font styles to use
Sans Serif

Colors
0054AA
0677BA
7BADD7
CADEEF
E8F1F8

Requirements
Must have
• My logo
Should not have
• any other pictures or images besides my logo

```html
<!DOCTYPE html>
<html lang="en">
<head>
<meta charset="utf-8">
<title>Kestrel Facilities Business Card</title>
<link href="https://fonts.googleapis.com/css2?family=Oswald:wght@400;500&family=Arimo:wght@400&display=swap" rel="stylesheet">
<style>
  :root {
    --stage: #888888;
    --card-white: #ffffff;
    --card-black: #000000;
    --brand-blue: #0a7fe0;
    --ink: #111111;
    --paper-text: #ffffff;
  }
  * { margin: 0; padding: 0; box-sizing: border-box; }
  html, body { width: 1075px; height: 1200px; overflow: hidden; }
  body { background: var(--stage); position: relative; font-family: "Arimo", Arial, sans-serif; }

  .card {
    position: absolute;
    left: 206px;
    width: 663px;
    height: 396px;
    box-shadow: 3px 3px 2px rgba(0,0,0,.55);
    overflow: hidden;
  }
  .card--front { top: 187px; background: var(--card-white); }
  .card--back { top: 637px; background: var(--card-black); }

  .front-band {
    position: absolute; left: 0; top: 260px; width: 100%; height: 136px;
    background: var(--card-black);
  }

  .brand {
    position: absolute;
    display: flex;
    align-items: center;
  }
  .brand-square { background: var(--brand-blue); flex: none; }
  .brand-name {
    font-family: "Oswald", sans-serif;
    font-weight: 500;
    color: var(--brand-blue);
    text-transform: uppercase;
    line-height: 1;
  }
  .brand-name span { display: block; }

  .brand--front { right: 40px; top: 52px; height: 159px; gap: 14px; }
  .brand--front .brand-square { width: 110px; height: 110px; }
  .brand--front .brand-name { font-size: 46px; }

  .brand--back { left: 0; right: 0; top: 96px; height: 203px; justify-content: center; gap: 22px; }
  .brand--back .brand-square { width: 170px; height: 170px; }
  .brand--back .brand-name { font-size: 66px; }

  .person-name {
    position: absolute; left: 35px; top: 191px;
    font-family: "Oswald", sans-serif; font-weight: 400;
    font-size: 29px; color: var(--brand-blue); letter-spacing: -.5px;
    text-transform: uppercase; line-height: 1;
  }
  .person-title {
    position: absolute; left: 35px; top: 222px;
    font-size: 18px; color: var(--ink);
  }
  .name-rule {
    position: absolute; left: 35px; top: 255px; width: 182px; height: 5px;
    background: var(--brand-blue);
  }

  .contact-list {
    position: absolute; left: 35px; top: 292px; list-style: none;
    color: var(--paper-text); font-size: 18px; line-height: 24px;
  }
  .contact-list li { display: flex; align-items: center; gap: 6px; }
  .contact-list svg { width: 17px; height: 17px; fill: var(--brand-blue); flex: none; }

  .address {
    position: absolute; right: 40px; top: 319px; text-align: right;
    color: var(--paper-text); font-size: 18px; line-height: 24px; font-style: normal;
  }
</style>
</head>
<body>
  <section class="card card--front">
    <div class="brand brand--front">
      <div class="brand-square"></div>
      <div class="brand-name"><span>Kestrel</span><span>Facilities</span></div>
    </div>

    <h1 class="person-name">Marcus Hale</h1>
    <p class="person-title">Managing Director</p>
    <div class="name-rule"></div>

    <div class="front-band"></div>

    <ul class="contact-list">
      <li>
        <svg viewBox="0 0 24 24" aria-hidden="true"><path d="M6.6 10.8a15.1 15.1 0 0 0 6.6 6.6l2.2-2.2a1 1 0 0 1 1-.25 11.4 11.4 0 0 0 3.6.57 1 1 0 0 1 1 1V20a1 1 0 0 1-1 1A17 17 0 0 1 3 4a1 1 0 0 1 1-1h3.5a1 1 0 0 1 1 1c0 1.25.2 2.45.57 3.57a1 1 0 0 1-.25 1z"/></svg>
        044-287 315 460
      </li>
      <li>
        <svg viewBox="0 0 24 24" aria-hidden="true"><path d="M2 5h20v14H2z M3.5 6.5 12 13l8.5-6.5" stroke="#000" stroke-width="1.5"/></svg>
        hello@kestrelfm.com
      </li>
      <li>
        <svg viewBox="0 0 24 24" aria-hidden="true"><path d="M12 2a10 10 0 1 0 0 20 10 10 0 0 0 0-20zm0 1.8c1.2 1.3 2 3.3 2.2 5.4H9.8C10 7.1 10.8 5.1 12 3.8zM8 9.2H4.1a8.2 8.2 0 0 1 5-5A11 11 0 0 0 8 9.2zm0 1.6a16 16 0 0 0 0 2.4H3.9a8 8 0 0 1 0-2.4zm1.6 0h4.8a14 14 0 0 1 0 2.4H9.6a14 14 0 0 1 0-2.4zm6.4 0h4.1a8 8 0 0 1 0 2.4H16a16 16 0 0 0 0-2.4zm-.1-1.6a11 11 0 0 0-1-5 8.2 8.2 0 0 1 5 5zM4.1 14.8H8a11 11 0 0 0 1.1 5 8.2 8.2 0 0 1-5-5zm5.7 0h4.4c-.2 2.1-1 4.1-2.2 5.4-1.2-1.3-2-3.3-2.2-5.4zm6.1 0h4a8.2 8.2 0 0 1-5 5 11 11 0 0 0 1-5z"/></svg>
        www.kestrelfm.com
      </li>
    </ul>

    <address class="address">18 Harrow Lane, Suite 402<br>30917, Northbridge</address>
  </section>

  <section class="card card--back">
    <div class="brand brand--back">
      <div class="brand-square"></div>
      <div class="brand-name"><span>Kestrel</span><span>Facilities</span></div>
    </div>
  </section>
</body>
</html>
```